Workshop PPT Update for AI Transformation Sessions

Our strategic consulting firm runs strategy workshops using slides as workshop exercises. These slides are used to communicate to the participants in advance, run the workshops and produce the final deliverable.

It is time for a design "upgrade". We'd like them to be more engaging, hipper and more interesting. These slides are utilitarian, so clean and usable is good. I have attached the example of what we have today. I have also attached an example of another company's slides that I like.

We can't rip off their design nor can we go away 100% from what we have. But I think it is possible to "update" our look to something closer to their look. Grey colors are fine with some color pop.

Slide styles needed are - 1) Cover Page, 2) Instructions Page, 3) Bullet list 4) Worksheet (place for participants to add content 5) Table, 6) Two column.

```html
<!DOCTYPE html>
<html lang="en">
<head>
<meta charset="utf-8">
<title>AI Transformation Workshop Slides</title>
<link href="https://fonts.googleapis.com/css2?family=Fira+Sans:wght@300;400;500;600;700&display=swap" rel="stylesheet">
<style>
:root{
  --board:#9d9797;
  --slate:#3d4150;
  --slate-soft:#d6d7db;
  --red:#b0443f;
  --red-soft:#c9b4b8;
  --ink:#2b2d36;
  --muted:#5d606b;
  --white:#ffffff;
}
*{margin:0;padding:0;box-sizing:border-box}
html,body{width:1200px;height:1096px;overflow:hidden}
body{background:radial-gradient(ellipse at 50% 40%,#a7a1a1,var(--board));font-family:"Fira Sans",sans-serif;color:var(--ink);position:relative}
.slide{position:absolute;width:876px;height:493px;background:var(--white);overflow:hidden;transform:scale(.5952);transform-origin:0 0;box-shadow:0 20px 40px rgba(0,0,0,.35)}
.abs{position:absolute}
.frame{position:absolute;inset:0;width:876px;height:493px}
.side-title{position:absolute;left:0;top:0;width:120px;height:493px;display:flex;align-items:center;justify-content:center}
.side-title span{writing-mode:vertical-rl;transform:rotate(180deg);color:var(--white);font-size:37px;font-weight:600;white-space:nowrap;letter-spacing:.2px}
.brand{position:absolute;top:455px;font-size:23px;font-weight:400;color:#4a4d58;letter-spacing:-.3px}
.copy{position:absolute;left:560px;top:474px;width:240px;text-align:center;color:var(--white);font-size:10px}
.page-no{position:absolute;left:837px;top:458px;width:30px;height:30px;border-radius:50%;background:var(--white);color:var(--red);font-size:12px;font-weight:600;display:flex;align-items:center;justify-content:center}
.step-badge{position:absolute;width:104px;height:104px;border-radius:50%}
.step-label{position:absolute;width:220px;text-align:center;font-size:15.5px;font-weight:500;line-height:21px;color:var(--ink)}
.h-main{font-size:28px;font-weight:500;color:var(--ink)}
.check-item{position:absolute;left:181px;font-size:11px;color:var(--ink);display:flex;gap:5px;line-height:16px}
.check-item i{display:inline-block;width:10px;height:10px;border:1px solid #666;margin-top:2px;flex:none}
.step-o{position:absolute;left:433px;font-size:16.5px;font-weight:600;color:var(--ink)}
.step-o b{color:var(--red);font-style:italic;font-weight:500;margin-right:6px}
.step-o small{display:block;font-size:12.5px;font-weight:400;margin-left:21px;margin-top:2px}
.principle-box{position:absolute;width:62px;height:62px;border-radius:4px;display:flex;align-items:center;justify-content:center}
.principle-box.dark{background:var(--slate)}
.principle-box.red{background:var(--red)}
.principle{position:absolute;width:240px}
.principle h3{font-size:18px;font-weight:500;margin-bottom:10px}
.principle p{font-size:12.3px;line-height:18px;color:var(--ink)}
.flow-dot{position:absolute;width:40px;height:40px;border-radius:50%;color:var(--white);font-size:15px;font-weight:500;display:flex;align-items:center;justify-content:center}
.flow-dot.red{background:var(--red)}
.flow-dot.light{background:var(--red-soft)}
.flow-dot.dark{background:var(--slate)}
.flow-item{position:absolute;width:220px}
.flow-item h4{font-size:13px;font-weight:500;line-height:15px}
.flow-item p{font-size:9.5px;color:var(--muted);line-height:14px;margin-top:4px}
.flow-item.right-align{text-align:right}
.plan-table{position:absolute;left:183px;top:97px;width:668px;border-collapse:collapse;font-size:11px;background:rgba(255,255,255,.85)}
.plan-table th{background:var(--slate);color:var(--white);font-weight:500;font-size:10.5px;text-align:left;padding:0 10px;height:48px;border-right:1px solid #6a6d78}
.plan-table td{height:47px;padding:0 10px;border:1px solid #d9d9dc;vertical-align:middle;color:var(--ink)}
</style>
</head>
<body>

<!-- Slide 01: Getting Started -->
<section class="slide" style="left:67px;top:78px">
  <div class="abs" role="img" aria-label="Photo of a business meeting with a laptop showing a bar chart" style="left:380px;top:0;width:496px;height:493px;background:linear-gradient(90deg,#ffffff 0%,rgba(236,234,232,.7) 25%,#d9d6d3 55%,#c7c4c2 100%)"></div>
  <svg class="frame" viewBox="0 0 876 493">
    <path d="M0 0H96C152 130 152 360 96 493H0Z" fill="var(--slate-soft)"/>
    <path d="M0 0H80C136 130 136 360 80 493H0Z" fill="var(--slate)"/>
    <path d="M545 493L556 466H876V493Z" fill="var(--red)"/>
  </svg>
  <div class="step-badge" role="img" aria-label="Step 1 badge with survey icon" style="left:216px;top:52px;background:radial-gradient(circle,#f7902d 0%,#f3a65e 55%,#f6d9c6 100%)"></div>
  <div class="step-badge" role="img" aria-label="Step 2 badge with folder icon" style="left:441px;top:52px;background:radial-gradient(circle,#1597e0 0%,#5ab4e8 55%,#d3e8f5 100%)"></div>
  <div class="step-badge" role="img" aria-label="Step 3 badge with calendar icon" style="left:216px;top:237px;background:radial-gradient(circle,#4a54b8 0%,#7c84cf 55%,#dcdef2 100%)"></div>
  <div class="step-badge" role="img" aria-label="Step 4 badge with checked invite icon" style="left:441px;top:237px;background:radial-gradient(circle,#d94b9c 0%,#e27fb8 55%,#f5dbe9 100%)"></div>
  <div class="side-title"><span>Getting Started</span></div>
  <p class="step-label" style="left:158px;top:167px">Complete the Engagement<br>Sizing Survey.</p>
  <p class="step-label" style="left:383px;top:167px">Collect relevant inputs.</p>
  <p class="step-label" style="left:158px;top:350px">Determine workshop<br>participants &amp; date.</p>
  <p class="step-label" style="left:383px;top:350px">Send invites, to include<br>pre-work</p>
  <div class="brand" style="left:143px">ClearPath</div>
  <div class="copy">© 2024 ClearPath. All Rights Reserved</div>
  <div class="page-no">01</div>
</section>

<!-- Slide 04: Principles instructions -->
<section class="slide" style="left:611px;top:78px">
  <svg class="frame" viewBox="0 0 876 493">
    <path d="M0 0H96C152 130 152 360 96 493H0Z" fill="var(--slate-soft)"/>
    <path d="M0 0H80C136 130 136 360 80 493H0Z" fill="var(--slate)"/>
    <path d="M545 493L556 466H876V493Z" fill="var(--red)"/>
  </svg>
  <div class="side-title"><span>Principles</span></div>
  <h1 class="abs h-main" style="left:181px;top:28px">Creating your AI Guiding Principles</h1>
  <h2 class="abs" style="left:181px;top:77px;font-size:14.5px;font-weight:500">Your Existing Material</h2>
  <div class="check-item" style="top:112px"><i></i>Company Values</div>
  <div class="check-item" style="top:145px"><i></i>Current Policies (GDPR,<br>CCPA, etc.)</div>
  <div class="check-item" style="top:194px"><i></i>Legal Guidance</div>
  <div class="check-item" style="top:226px"><i></i>OTHER</div>
  <h2 class="abs" style="left:196px;top:256px;font-size:14.5px;font-weight:500">Examples for Inspiration</h2>
  <p class="abs" style="left:196px;top:292px;font-size:11px">See next slides</p>
  <h2 class="abs" style="left:196px;top:321px;font-size:14.5px;font-weight:500">AI Chat Prompts</h2>
  <p class="abs" style="left:196px;top:357px;font-size:11px">HERE</p>
  <p class="abs" style="left:425px;top:83px;width:360px;font-size:11.5px;line-height:21px"><span style="color:var(--red);font-size:17px;font-weight:500">Purpose:</span> To create behavioral statements that everyone is expected to adhere to.</p>
  <h2 class="abs" style="left:424px;top:134px;font-size:23px;font-weight:500">INSTRUCTIONS</h2>
  <div class="step-o" style="top:178px"><b>O</b>Create the Outline.<small>Determine the topics that need a principle.</small></div>
  <div class="step-o" style="top:231px"><b>O</b>Audit the Outline.<small>Look at the current policies to determine if all topics are covered.</small></div>
  <div class="step-o" style="top:284px"><b>O</b>Draft the Guiding Principles.</div>
  <div class="step-o" style="top:319px"><b>O</b>Determine which GPs need detailed policies.</div>
  <div class="step-o" style="top:354px"><b>O</b>Determine which AI Tools support the GPs.</div>
  <div class="step-o" style="top:389px"><b>O</b>Finalize via a legal and executive review.</div>
  <div class="brand" style="left:116px">ClearPath</div>
  <div class="copy">© 2024 ClearPath. All Rights Reserved</div>
  <div class="page-no">04</div>
</section>

<!-- Slide 02: Kickoff cover -->
<section class="slide" style="left:67px;top:401px">
  <div class="abs" role="img" aria-label="Surreal illustration of a figure wearing a VR headset amid clouds, planets and sea" style="left:70px;top:0;width:806px;height:493px;background:linear-gradient(135deg,#e8a27a 0%,#c45a4a 25%,#2d6c7a 55%,#1d4a57 80%,#123841 100%)"></div>
  <svg class="frame" viewBox="0 0 876 493">
    <path d="M0 0H96C152 130 152 360 96 493H0Z" fill="var(--slate-soft)"/>
    <path d="M0 0H80C136 130 136 360 80 493H0Z" fill="var(--slate)"/>
    <path d="M545 493L556 466H876V493Z" fill="var(--red)"/>
  </svg>
  <div class="side-title"><span>Kickoff &amp; Discovery</span></div>
  <div class="abs" style="left:164px;top:310px;width:712px;height:117px;background:rgba(61,65,80,.92)"></div>
  <h1 class="abs" style="left:196px;top:320px;color:#fff;font-size:38px;font-weight:600">Kickoff &amp; Discovery</h1>
  <p class="abs" style="left:196px;top:378px;color:#fff;font-size:25px;font-weight:300">Sizing &amp; Scoping AI Transformation</p>
  <div class="brand" style="left:116px;color:#fff">ClearPath</div>
  <div class="copy">© 2024 ClearPath. All Rights Reserved</div>
  <div class="page-no">02</div>
</section>

<!-- Slide 05: AI Guiding Principles -->
<section class="slide" style="left:611px;top:401px">
  <div class="abs" role="img" aria-label="Faint circuit board decoration around the letters AI" style="left:520px;top:150px;width:356px;height:310px;background:radial-gradient(circle at 55% 55%,#ececee 0%,#f5f5f6 45%,#ffffff 75%)"></div>
  <svg class="frame" viewBox="0 0 876 493">
    <path d="M0 0H96C152 130 152 360 96 493H0Z" fill="var(--slate-soft)"/>
    <path d="M0 0H80C136 130 136 360 80 493H0Z" fill="var(--slate)"/>
    <path d="M545 493L556 466H876V493Z" fill="var(--red)"/>
  </svg>
  <div class="side-title"><span>AI Guiding Principles</span></div>

  <div class="principle-box dark" style="left:172px;top:31px"><svg width="32" height="26" viewBox="0 0 32 26"><path d="M3 13l9 9L29 4" fill="none" stroke="#fff" stroke-width="5"/></svg></div>
  <div class="principle" style="left:258px;top:26px"><h3>Principle #1</h3><p>Complete perspective from Executives, Directors, Managers &amp; Staff. Conduct competitive analysis and customer research (optional).</p></div>

  <div class="principle-box red" style="left:549px;top:31px"><svg width="32" height="26" viewBox="0 0 32 26"><path d="M3 13l9 9L29 4" fill="none" stroke="#fff" stroke-width="5"/></svg></div>
  <div class="principle" style="left:635px;top:26px"><h3>Principle #2</h3><p>Complete perspective from Executives, Directors, Managers &amp; Staff. Conduct competitive analysis and customer research (optional)</p></div>

  <div class="principle-box red" style="left:172px;top:179px"><svg width="32" height="26" viewBox="0 0 32 26"><path d="M3 13l9 9L29 4" fill="none" stroke="#fff" stroke-width="5"/></svg></div>
  <div class="principle" style="left:258px;top:174px"><h3>Principle #3</h3><p>Complete perspective from Executives, Directors, Managers &amp; Staff. Conduct competitive analysis and customer research (optional).</p></div>

  <div class="principle-box dark" style="left:549px;top:179px"><svg width="32" height="26" viewBox="0 0 32 26"><path d="M3 13l9 9L29 4" fill="none" stroke="#fff" stroke-width="5"/></svg></div>
  <div class="principle" style="left:635px;top:174px"><h3>Principle #4</h3><p>Complete perspective from Executives, Directors, Managers &amp; Staff. Conduct competitive analysis and customer research (optional).</p></div>

  <div class="principle-box dark" style="left:172px;top:327px"><svg width="32" height="26" viewBox="0 0 32 26"><path d="M3 13l9 9L29 4" fill="none" stroke="#fff" stroke-width="5"/></svg></div>
  <div class="principle" style="left:258px;top:322px"><h3>Principle #5</h3><p>Complete perspective from Executives, Directors, Managers &amp; Staff. Conduct competitive analysis and customer research (optional).</p></div>

  <div class="brand" style="left:116px">ClearPath</div>
  <p class="abs" style="left:266px;top:467px;font-size:11px">What guides our decision-making and approach?</p>
  <div class="copy">© 2024 ClearPath. All Rights Reserved</div>
  <div class="page-no">05</div>
</section>

<!-- Slide 03: Workshop Overview -->
<section class="slide" style="left:67px;top:724px">
  <svg class="frame" viewBox="0 0 876 493">
    <path d="M0 0H96C152 130 152 360 96 493H0Z" fill="var(--slate-soft)"/>
    <path d="M0 0H80C136 130 136 360 80 493H0Z" fill="var(--slate)"/>
    <path d="M545 493L556 466H876V493Z" fill="var(--red)"/>
    <circle cx="505" cy="309" r="103" fill="#fff" stroke="#b77d80" stroke-width="1.5"/>
    <path d="M425 226A122 122 0 0 0 425 392" fill="none" stroke="#c9c9cd" stroke-width="1.5"/>
    <path d="M585 226A122 122 0 0 1 585 392" fill="none" stroke="#c9c9cd" stroke-width="1.5"/>
  </svg>
  <div class="side-title"><span>Workshop Overview</span></div>
  <p class="abs" style="left:164px;top:22px;font-size:26px;font-weight:600">Participants: Execs</p>
  <p class="abs" style="left:412px;top:22px;font-size:26px;font-weight:300">Duration: 2 hrs.</p>
  <p class="abs" style="left:164px;top:65px;font-size:15px;word-spacing:2px"><span style="color:var(--red);font-weight:500">Prep Work:</span>&nbsp;&nbsp;Org Strategy&nbsp;&nbsp;&nbsp;&nbsp;2023 Goal Performance&nbsp;&nbsp;&nbsp;&nbsp;Existing policies&nbsp;&nbsp;&nbsp;&nbsp;Pre-thinking questions</p>
  <h2 class="abs" style="left:360px;top:122px;width:300px;text-align:center;font-size:24px;font-weight:500">Workshop Flow</h2>
  <p class="abs" style="left:405px;top:295px;width:200px;text-align:center;font-size:24px;color:#4a4d58">ClearPath</p>

  <div class="flow-dot red" style="left:397px;top:194px">01</div>
  <div class="flow-dot light" style="left:358px;top:291px">02</div>
  <div class="flow-dot dark" style="left:397px;top:384px">03</div>
  <div class="flow-dot red" style="left:576px;top:194px">04</div>
  <div class="flow-dot light" style="left:616px;top:291px">05</div>
  <div class="flow-dot dark" style="left:576px;top:384px">06</div>

  <div class="flow-item right-align" style="left:170px;top:186px"><h4>Confirm Company<br>Direction</h4><p>Recap organizational purpose, values,<br>vision &amp; winning strategy.</p></div>
  <div class="flow-item right-align" style="left:130px;top:302px"><h4>Develop AI Vision</h4></div>
  <div class="flow-item right-align" style="left:165px;top:390px"><h4>Develop AI Guiding Principles</h4><p>Developed AI Guiding Principles, supporting<br>policies to include approved tools.</p></div>
  <div class="flow-item" style="left:632px;top:186px"><h4>Agree on a Governance Approach</h4><p>Agreed upon governance approach,<br>structure, &amp; executive champion.</p></div>
  <div class="flow-item" style="left:668px;top:282px"><h4>Agree on a Training &amp; Learning<br>Approach</h4><p>Set approach to training &amp; continuous<br>learning.</p></div>
  <div class="flow-item" style="left:632px;top:393px"><h4>Determine Rollout &amp; Communication</h4><p>Organizational rollout &amp; continuous<br>communication.</p></div>

  <div class="brand" style="left:116px">ClearPath</div>
  <p class="abs" style="left:287px;top:471px;font-size:10px"><b style="font-weight:600">Deliverables</b>&nbsp;&nbsp;<i>Your Company's AI Playbook</i></p>
  <div class="copy">© 2024 ClearPath. All Rights Reserved</div>
  <div class="page-no">03</div>
</section>

<!-- Slide 06: Plan Structure -->
<section class="slide" style="left:611px;top:724px">
  <div class="abs" role="img" aria-label="Faint photo of a person facing a maze with an upward arrow" style="left:80px;top:0;width:796px;height:493px;background:linear-gradient(180deg,#ecebea 0%,#f6f6f5 35%,#f3f3f3 65%,#e4e4e5 100%)"></div>
  <svg class="frame" viewBox="0 0 876 493">
    <path d="M0 0H96C152 130 152 360 96 493H0Z" fill="var(--slate-soft)"/>
    <path d="M0 0H80C136 130 136 360 80 493H0Z" fill="var(--slate)"/>
    <path d="M545 493L556 466H876V493Z" fill="var(--red)"/>
  </svg>
  <div class="side-title"><span>Plan Structure</span></div>
  <h1 class="abs" style="left:182px;top:50px;font-size:25px;font-weight:500">Plan Structure</h1>
  <table class="plan-table">
    <colgroup><col style="width:40px"><col style="width:81px"><col style="width:220px"><col style="width:169px"><col style="width:158px"></colgroup>
    <thead>
      <tr><th colspan="2" style="text-align:center">LEVEL</th><th>PLANNING ELEMENT &amp; DEFINITION</th><th>ACCOUNTABILITY/OWNER</th><th>FREQUENCY OF<br>MODIFICATION</th></tr>
    </thead>
    <tbody>
      <tr><td style="padding:0 4px;text-align:center">1</td><td style="text-align:center">What<br>(overall)</td><td style="font-weight:500">Strategic Priorities</td><td style="font-weight:500">N/A</td><td style="font-weight:500">3+ YEARS</td></tr>
      <tr><td style="padding:0 4px;text-align:center">1.1</td><td style="text-align:center;line-height:24px">What<br>How</td><td style="line-height:20px"><b style="font-weight:500">Goals</b><br>Outcomes &amp; Strategies</td><td style="font-weight:500">EXECUTIVE LEADERSHIP</td><td style="font-weight:500">1-3 YEARS</td></tr>
      <tr><td style="padding:0 4px;text-align:center">1.1.1</td><td></td><td style="font-weight:500">Key Performance Indicators<br>and/or Initiatives</td><td></td><td style="font-weight:500">1 year<br>(w/ qrtly targets)</td></tr>
      <tr><td style="padding:0 4px;text-align:center">1.1.1.1</td><td></td><td>Action Items</td><td></td><td>Quarterly/Monthly</td></tr>
    </tbody>
  </table>
  <div class="brand" style="left:116px">ClearPath</div>
  <div class="copy">© 2024 ClearPath. All Rights Reserved</div>
  <div class="page-no">06</div>
</section>

</body>
</html>
```